Best local air conditioning and heating contractor

We need a website design for a new company in Tampa Bay called the Coastal Breeze Cooling Company. We provide superior services for residential and commercial properties as well as maintenance and installing HVAC systems. We also want to sell equipment, parts and filter on the website as well. We want it easy to use for customers. Rich with content and keywords for our area.

Target Market(s)

homeowners in Tampa Bay

Industry/Entity Type

HVAC air conditioning and heating

Coding

Coded - Design and coding required

Number of Pages Required

5+ page

Font styles to use
Sans Serif

Requirements
Nice to have
• would like the colors to be same as logo

```html
<!DOCTYPE html>
<html lang="en">
<head>
<meta charset="utf-8">
<title>Coastal Breeze Cooling Company</title>
<link rel="stylesheet" href="https://fonts.googleapis.com/css2?family=Michroma&family=Oswald:wght@400;500;600&family=Open+Sans:wght@400;600&display=swap">
<style>
:root{
  --navy:#24336b;
  --navy-dark:#1b2858;
  --red:#d8232f;
  --ink:#333;
  --muted:#555;
  --white:#fff;
  --black:#0d0d0d;
  --gold:#f2c200;
}
*{box-sizing:border-box;margin:0;padding:0}
html,body{width:1200px;height:4587px;overflow:hidden}
body{font-family:"Open Sans",sans-serif;color:var(--ink);background:var(--white);position:relative}
.abs{position:absolute}
a{color:inherit;text-decoration:none}

/* header */
.site-header{position:absolute;top:0;left:0;width:1200px;height:100px;background:#fff}
.topbar{position:absolute;left:415px;top:0;right:0;height:52px;background:var(--navy);border-bottom-left-radius:40px;color:#fff;font-size:16px;display:flex;align-items:center;gap:48px;padding-left:122px}
.topbar span{display:flex;align-items:center;gap:14px}
.topbar .ico{width:34px;height:34px;border-radius:50%;background:#fff;display:flex;align-items:center;justify-content:center}
.brand{position:absolute;left:98px;top:24px;display:flex;align-items:center;gap:10px}
.brand .dot{width:44px;height:44px;border-radius:50%;background:var(--red)}
.brand .name{font-family:"Oswald",sans-serif;font-weight:600;font-size:18px;line-height:1.1;color:var(--navy);width:150px}
.nav{position:absolute;top:62px;left:561px;display:flex;gap:42px;font-family:"Oswald",sans-serif;font-size:16px;color:#222}
.nav .active{color:var(--red);text-decoration:underline;text-underline-offset:4px}

/* hero */
.hero{top:100px;left:0;width:1200px;height:600px}
.hero-photo{position:absolute;inset:0;background:linear-gradient(90deg,#f2f2f2 0%,#e6e6e6 45%,#b9bcc0 70%,#d9d9d6 100%)}
.hero h1{position:absolute;left:98px;top:150px;font-family:"Michroma",sans-serif;font-size:46px;color:var(--navy);letter-spacing:1px}
.hero h1 em{font-style:normal;color:var(--red)}
.hero h2{position:absolute;left:98px;top:228px;font-family:"Oswald",sans-serif;font-weight:500;font-size:21px;color:var(--navy);letter-spacing:.5px}
.hero p{position:absolute;left:98px;top:268px;width:340px;font-family:"Oswald",sans-serif;font-size:15px;line-height:31px;color:#222}
.btn-navy{background:var(--navy);color:#fff;font-family:"Michroma",sans-serif;font-size:15px;display:flex;align-items:center;justify-content:center}
.hero .btn-navy{position:absolute;left:98px;top:380px;width:168px;height:48px}
.review-bubble{position:absolute;left:680px;top:128px;width:144px;height:70px;background:#fff;border-radius:35px;box-shadow:0 3px 10px rgba(0,0,0,.15);text-align:center;font-size:12px;padding-top:10px;line-height:17px}
.review-bubble .stars{color:var(--gold);letter-spacing:2px}

/* section titles */
.sec-mark{width:36px;height:36px;border-radius:50%;background:var(--red);margin:0 auto}
.sec-title{display:flex;align-items:center;justify-content:center;gap:14px;font-family:"Michroma",sans-serif;font-size:32px;color:var(--navy)}
.sec-title::before,.sec-title::after{content:"";width:48px;height:3px;background:var(--red)}
.sec-title em{font-style:normal;color:var(--red)}

/* shop */
.shop{top:700px;left:0;width:1200px;height:708px}
.shop .sec-mark{position:absolute;left:582px;top:106px}
.shop .sec-title{position:absolute;top:150px;width:1200px}
.shop-card{position:absolute;top:225px;width:232px;height:350px;text-align:center;color:#fff}
.shop-card svg.shape{position:absolute;inset:0}
.shop-card .icon{position:absolute;left:67px;top:65px;width:98px;height:98px;border-radius:50%;background:#fff;display:flex;align-items:center;justify-content:center}
.shop-card h3{position:absolute;top:180px;width:100%;font-family:"Oswald",sans-serif;font-weight:500;font-size:19px}
.shop-card p{position:absolute;top:215px;left:14px;right:14px;font-size:14px;line-height:31px}
.shop-card .more{position:absolute;top:305px;width:100%;font-family:"Oswald",sans-serif;font-size:16px}

/* about */
.about{top:1408px;left:0;width:1200px;height:594px;background:linear-gradient(90deg,var(--navy-dark),var(--navy))}
.about h2{position:absolute;left:98px;top:82px;font-family:"Michroma",sans-serif;font-size:30px;line-height:42px;color:#fff;font-weight:400}
.about p{position:absolute;left:98px;top:208px;width:476px;font-size:14px;line-height:31px;color:#fff}
.btn-white{position:absolute;left:98px;top:442px;width:144px;height:48px;background:#fff;color:var(--navy);font-family:"Michroma",sans-serif;font-size:15px;display:flex;align-items:center;justify-content:center}
.about .frame{position:absolute;left:620px;top:110px;width:473px;height:382px;border:2px solid #fff}
.about .photo{position:absolute;left:634px;top:100px;width:467px;height:382px;background:linear-gradient(120deg,#4f6a3a,#7e7c72 45%,#2d3040)}
.dots{position:absolute;left:1010px;top:72px;width:120px;height:120px;background-image:radial-gradient(#fff 2px,transparent 2.5px);background-size:20px 20px}

/* services */
.services{top:2002px;left:0;width:1200px;height:918px}
.services .sec-mark{position:absolute;left:582px;top:94px}
.services .sec-title{position:absolute;top:136px;width:1200px}
.services .lead{position:absolute;top:196px;left:170px;width:860px;text-align:center;font-family:"Oswald",sans-serif;font-size:15px;line-height:31px;color:#333}
.svc-card{position:absolute;top:300px;width:317px;height:497px;background:#fff;box-shadow:0 3px 14px rgba(0,0,0,.14);text-align:center}
.svc-card .photo{position:absolute;left:13px;top:13px;width:291px;height:205px}
.svc-card .badge{position:absolute;left:113px;top:190px;width:90px;height:90px;border-radius:50%;background:var(--navy);border:4px solid #fff;display:flex;align-items:center;justify-content:center}
.svc-card h3{position:absolute;top:290px;width:100%;font-family:"Michroma",sans-serif;font-size:19px;color:#111;font-weight:400}
.svc-card p{position:absolute;top:330px;left:18px;right:18px;font-size:14px;line-height:26px;color:#444}
.btn-outline{position:absolute;left:88px;top:420px;width:142px;height:48px;border:2px solid var(--red);color:var(--red);font-family:"Oswald",sans-serif;font-size:17px;display:flex;align-items:center;justify-content:center}

/* request */
.request{top:2920px;left:0;width:1200px;height:572px;background:var(--navy)}
.request .photo{position:absolute;left:0;top:0;width:600px;height:572px;background:linear-gradient(90deg,#7a8aa0,#4f6079 60%,var(--navy))}
.request h2{position:absolute;left:542px;top:70px;font-family:"Michroma",sans-serif;font-size:26px;color:#fff;font-weight:400}
.field{position:absolute;height:42px;background:#fff;font-size:13px;color:#444;padding:12px 12px;border:1px solid #ccc}
.submit{position:absolute;left:542px;top:457px;width:126px;height:38px;background:var(--red);color:#fff;font-family:"Michroma",sans-serif;font-size:14px;display:flex;align-items:center;justify-content:center}

/* testimonials */
.testimonials{top:3492px;left:0;width:1200px;height:668px}
.testimonials .sec-mark{position:absolute;left:582px;top:86px}
.testimonials .sec-title{position:absolute;top:128px;width:1200px}
.t-card{position:absolute;top:258px;width:310px;height:200px;background:#fff;border-top:3px solid var(--navy);border-radius:18px;box-shadow:0 4px 14px rgba(0,0,0,.12);text-align:center}
.t-card .avatar{position:absolute;left:110px;top:-52px;width:90px;height:90px;border-radius:50%;background:linear-gradient(#d9dde3,#9aa4b3);border:3px solid #fff}
.t-card p{position:absolute;top:66px;left:20px;right:20px;font-size:14px;line-height:26px;color:#444}
.t-name{position:absolute;top:480px;font-size:15px;color:#222;display:flex;gap:30px}
.t-name .stars{color:var(--gold);letter-spacing:1px}
.testimonials .btn-navy{position:absolute;left:495px;top:538px;width:204px;height:46px;font-family:"Oswald",sans-serif;font-size:15px}

/* footer */
.site-footer{top:4160px;left:0;width:1200px;height:427px;background:var(--black);color:#fff}
.site-footer h4{font-family:"Oswald",sans-serif;font-weight:500;font-size:21px;margin-bottom:12px}
.f-col{position:absolute;top:70px}
.f-col ul{list-style:none;font-size:14px;line-height:31px}
.f-col li::before{content:"➜";margin-right:12px;font-size:13px}
.contact-row{display:flex;align-items:center;gap:16px;font-size:15px;margin-bottom:22px}
.contact-row .ico{width:36px;height:36px;border-radius:50%;background:var(--red);display:flex;align-items:center;justify-content:center}
.newsletter p{font-size:14px;line-height:28px;width:280px}
.newsletter .email{width:274px;border-bottom:1px solid #fff;font-size:14px;padding:6px 2px;margin-top:4px}
.newsletter .sub{margin-top:24px;margin-left:6px;width:146px;height:50px;border-radius:25px;background:var(--red);display:flex;align-items:center;justify-content:center;font-size:17px;font-weight:600}
.copyright{position:absolute;left:98px;right:98px;top:382px;border-top:1px solid #555;padding-top:18px;text-align:center;font-size:13px}
</style>
</head>
<body>

<header class="site-header">
  <div class="brand"><div class="dot"></div><div class="name">Coastal Breeze Cooling Company</div></div>
  <div class="topbar">
    <span><i class="ico"><svg width="16" height="16" viewBox="0 0 24 24"><path fill="#24336b" d="M6.6 10.8a15 15 0 0 0 6.6 6.6l2.2-2.2a1 1 0 0 1 1-.25 11.4 11.4 0 0 0 3.6.6 1 1 0 0 1 1 1V20a1 1 0 0 1-1 1A17 17 0 0 1 3 4a1 1 0 0 1 1-1h3.5a1 1 0 0 1 1 1c0 1.25.2 2.45.6 3.6a1 1 0 0 1-.25 1z"/></svg></i>+1 813 555 0142</span>
    <span><i class="ico"><svg width="16" height="16" viewBox="0 0 24 24"><path fill="#24336b" d="M3 5h18v14H3zm2 2v.5l7 4.5 7-4.5V7l-7 4.5z"/></svg></i>info@coastalbreezecooling.com</span>
  </div>
  <nav class="nav"><a class="active">Home</a><a>About Us</a><a>Services</a><a>Shop</a><a>Testimonials</a><a>Contact Us</a></nav>
</header>

<section class="hero abs">
  <div class="hero-photo" role="img" aria-label="Smiling man relaxing on a grey sofa with a laptop under a wall-mounted air conditioner, potted plant beside him"></div>
  <h1>COASTAL <em>BREEZE</em></h1>
  <h2>COOLING COMPANY.</h2>
  <p>Lorem ipsum dolor sit amet, consectetur adipiscing elit, sed do eiusmod tempor incididunt ut labore et dolore magna aliqua.</p>
  <a class="btn-navy">Learn More</a>
  <div class="review-bubble"><div class="stars">☆☆☆☆☆</div>450+ 5 Star<br>Reviews</div>
</section>

<section class="shop abs">
  <div class="sec-mark"></div>
  <h2 class="sec-title">OUR&nbsp;<em>SHOP</em></h2>

  <div class="shop-card" style="left:98px">
    <svg class="shape" width="232" height="350" viewBox="0 0 232 350"><path d="M0 60 116 0 232 60V350H0Z" fill="#d8232f"/><path d="M0 76 116 16 232 76V350H0Z" fill="#24336b"/></svg>
    <div class="icon"><svg width="50" height="50" viewBox="0 0 24 24"><circle cx="12" cy="8" r="4" fill="#f2c200"/><path d="M4 22c0-5 3.5-8 8-8s8 3 8 8z" fill="#24336b"/></svg></div>
    <h3>Sell Equipment</h3>
    <p>Lorem ipsum dolor sit amet, incididunt ut labore et dolore magna aliqua.</p>
  </div>

  <div class="shop-card" style="left:356px;height:362px">
    <svg class="shape" width="232" height="362" viewBox="0 0 232 362"><path d="M0 60 116 0 232 60V362H0Z" fill="#24336b"/><path d="M8 72 116 16 224 72V354H8Z" fill="#d8232f"/></svg>
    <div class="icon"><svg width="50" height="50" viewBox="0 0 24 24"><rect x="5" y="12" width="14" height="7" fill="#24336b"/><circle cx="9" cy="7" r="3" fill="none" stroke="#f2a000" stroke-width="2"/></svg></div>
    <h3>Parts</h3>
    <p>Lorem ipsum dolor sit amet, incididunt ut labore et dolore magna aliqua.</p>
    <div class="more">Read More ➜</div>
  </div>

  <div class="shop-card" style="left:613px">
    <svg class="shape" width="232" height="350" viewBox="0 0 232 350"><path d="M0 60 116 0 232 60V350H0Z" fill="#d8232f"/><path d="M0 76 116 16 232 76V350H0Z" fill="#24336b"/></svg>
    <div class="icon"><svg width="50" height="50" viewBox="0 0 24 24"><rect x="3" y="6" width="18" height="8" rx="1" fill="none" stroke="#24336b" stroke-width="1.6"/><circle cx="8" cy="16" r="4" fill="#4aa3df"/></svg></div>
    <h3>Filters</h3>
    <p>Lorem ipsum dolor sit amet, incididunt ut labore et dolore magna aliqua.</p>
  </div>

  <div class="shop-card" style="left:870px">
    <svg class="shape" width="232" height="350" viewBox="0 0 232 350"><path d="M0 60 116 0 232 60V350H0Z" fill="#d8232f"/><path d="M0 76 116 16 232 76V350H0Z" fill="#24336b"/></svg>
    <div class="icon"><svg width="50" height="50" viewBox="0 0 24 24"><rect x="6" y="5" width="12" height="8" transform="rotate(-20 12 9)" fill="#f2a000"/><path d="M2 17q3-3 5 0t5 0 5 0 5 0v4H2z" fill="#4aa3df"/></svg></div>
    <h3>HVAC systems</h3>
    <p>Lorem ipsum dolor sit amet, incididunt ut labore et dolore magna aliqua.</p>
  </div>
</section>

<section class="about abs">
  <h2>The Coastal Breeze<br>Cooling Company</h2>
  <p>Lorem ipsum dolor sit amet, consectetur adipiscing elit, sed do eiusmod tempor incididunt ut labore et dolore magna aliqua. Ut enim ad minim veniam, quis nostrud exercitation ullamco laboris nisi ut aliquip ex ea commodo consequat. Duis aute irure dolor in reprehenderit in voluptate velit esse cillum dolore eu fugiat nulla pariatur. Excepteur sint occaecat cupidatat non proident, sunt in culpa qui officia deserunt mollit anim id est laborum.</p>
  <a class="btn-white">Read More</a>
  <div class="dots"></div>
  <div class="frame"></div>
  <div class="photo" role="img" aria-label="Technician kneeling beside an outdoor air conditioning condenser unit, repairing it"></div>
</section>

<section class="services abs">
  <div class="sec-mark"></div>
  <h2 class="sec-title">Our Services</h2>
  <p class="lead">Lorem ipsum dolor sit amet, consectetur adipiscing elit, sed do eiusmod tempor incididunt ut labore et dolore magna aliqua. Ut enim ad minim veniam, quis nostrud exercitation ullamco laboris nisi ut aliquip ex ea commodo consequat.</p>

  <div class="svc-card" style="left:98px">
    <div class="photo" role="img" aria-label="Mother and daughter playing in a cool living room under an air conditioner" style="background:linear-gradient(135deg,#f3efe9,#d7c3b0)"></div>
    <div class="badge"><svg width="40" height="40" viewBox="0 0 24 24" fill="none" stroke="#fff" stroke-width="1.5"><rect x="3" y="5" width="18" height="7" rx="1"/><circle cx="9" cy="16" r="3"/></svg></div>
    <h3>Residential</h3>
    <p>Lorem ipsum dolor sit amet, consectetur adipiscing elit, sed do eiusmod tempor incididunt ut aliqua.</p>
    <a class="btn-outline">Read More</a>
  </div>

  <div class="svc-card" style="left:441px">
    <div class="photo" role="img" aria-label="Technician in a hard hat installing rooftop HVAC equipment" style="background:linear-gradient(135deg,#8aa9c9,#5d6571 60%,#c7c9cc)"></div>
    <div class="badge"><svg width="40" height="40" viewBox="0 0 24 24" fill="none" stroke="#fff" stroke-width="1.5"><rect x="4" y="10" width="16" height="10" rx="1"/><circle cx="9" cy="15" r="2.5"/><path d="M8 4h8v4H8z"/></svg></div>
    <h3>Installing HVAC systems</h3>
    <p>Lorem ipsum dolor sit amet, consectetur adipiscing elit, sed do eiusmod tempor incididunt ut aliqua.</p>
    <a class="btn-outline">Read More</a>
  </div>

  <div class="svc-card" style="left:785px">
    <div class="photo" role="img" aria-label="Commercial air conditioning units outside a glass office building" style="background:linear-gradient(135deg,#9fb6cf,#e6e8ea 55%,#6f8a57)"></div>
    <div class="badge"><svg width="40" height="40" viewBox="0 0 24 24" fill="none" stroke="#fff" stroke-width="1.5"><rect x="3" y="5" width="18" height="7" rx="1"/><path d="M8 15v4M12 15v4M16 15v4"/></svg></div>
    <h3>Commercial</h3>
    <p>Lorem ipsum dolor sit amet, consectetur adipiscing elit, sed do eiusmod tempor incididunt ut aliqua.</p>
    <a class="btn-outline">Read More</a>
  </div>
</section>

<section class="request abs">
  <div class="photo" role="img" aria-label="Smiling technician in a cap servicing a tankless water heater"></div>
  <h2>Request Service or an Estimate</h2>
  <div class="field" style="left:542px;top:150px;width:267px">Name</div>
  <div class="field" style="left:826px;top:150px;width:267px">Email</div>
  <div class="field" style="left:542px;top:212px;width:267px">Phone</div>
  <div class="field" style="left:826px;top:212px;width:267px">Address</div>
  <div class="field" style="left:542px;top:274px;width:267px">City/Town</div>
  <div class="field" style="left:826px;top:274px;width:267px">Service Needed<span style="float:right">▾</span></div>
  <div class="field" style="left:542px;top:344px;width:551px;height:88px">Comment</div>
  <a class="submit">Submit</a>
</section>

<section class="testimonials abs">
  <div class="sec-mark"></div>
  <h2 class="sec-title">Testimonials</h2>

  <div class="t-card" style="left:110px">
    <div class="avatar" role="img" aria-label="Customer portrait"></div>
    <p>“I have used them twice for plumbing issues. They arrived quickly...The plumbers they sent were professional and completed the job efficiently. ”</p>
  </div>
  <div class="t-name" style="left:198px"><span>Marisol T.</span><span class="stars">★★★★★</span></div>

  <div class="t-card" style="left:444px">
    <div class="avatar" role="img" aria-label="Customer portrait"></div>
    <p>“They were awesome when installing our tankless water heater. We liked their professionalism so much that I answering all my questions.”</p>
  </div>
  <div class="t-name" style="left:523px"><span>Dana K.</span><span class="stars">★★★★★</span></div>

  <div class="t-card" style="left:778px">
    <div class="avatar" role="img" aria-label="Customer portrait"></div>
    <p>“Jordan installed a new furnace for our house, did an excellent job. HVAC crew was very friendly and professional installation.”</p>
  </div>
  <div class="t-name" style="left:830px"><span>Jordan P.</span><span class="stars">★★★★★</span></div>

  <a class="btn-navy">More Customer Reviews</a>
</section>

<footer class="site-footer abs">
  <div class="f-col" style="left:98px"><h4>Quick Links</h4><ul><li>Home</li><li>About Us</li><li>Services</li><li>Shop</li><li>Testimonials</li><li>Contact Us</li></ul></div>
  <div class="f-col" style="left:296px"><h4>Other Links</h4><ul><li>FAQ</li><li>Terms of Use</li><li>Privacy Policy</li><li>Support Links</li><li>Conditions</li></ul></div>
  <div class="f-col" style="left:508px"><h4>Contact Us</h4>
    <div class="contact-row"><i class="ico"><svg width="16" height="16" viewBox="0 0 24 24"><path fill="#fff" d="M12 2a7 7 0 0 0-7 7c0 5 7 13 7 13s7-8 7-13a7 7 0 0 0-7-7zm0 9.5a2.5 2.5 0 1 1 0-5 2.5 2.5 0 0 1 0 5z"/></svg></i>Tampa Bay, United States.</div>
    <div class="contact-row"><i class="ico"><svg width="16" height="16" viewBox="0 0 24 24"><path fill="#fff" d="M3 5h18v14H3zm2 2v.5l7 4.5 7-4.5V7l-7 4.5z"/></svg></i>info@coastalbreeze.com</div>
    <div class="contact-row"><i class="ico"><svg width="16" height="16" viewBox="0 0 24 24"><path fill="#fff" d="M6.6 10.8a15 15 0 0 0 6.6 6.6l2.2-2.2a1 1 0 0 1 1-.25 11.4 11.4 0 0 0 3.6.6 1 1 0 0 1 1 1V20a1 1 0 0 1-1 1A17 17 0 0 1 3 4a1 1 0 0 1 1-1h3.5a1 1 0 0 1 1 1c0 1.25.2 2.45.6 3.6a1 1 0 0 1-.25 1z"/></svg></i>+1 813 555 0142</div>
  </div>
  <div class="f-col newsletter" style="left:828px"><h4>Sign Up To Our Newsletter</h4>
    <p>Lorem ipsum dolor sit amet,consectetur adipiscing elit,adipiscing elit.</p>
    <div class="email">Email</div>
    <a class="sub">Subscribe</a>
  </div>
  <div class="copyright">Copyrights@2024.The Coastal Breeze Cooling Company.All Rights Reserved</div>
</footer>

</body>
</html>
```